Harborline Lending and Capital. We provide MOSTLY residential home mortgages in Florida AND commercial loans for investment properties throughout the United states.
I would love to emulate so of the lender sites that are available on the internet but I would like to have the site as popular as possible for SEO purposes. Clients can already click the link to take them to the mortgage application where they can complete that and upload documents. If you could polish that up for me that would be great. I can also provide you with great detail on loan programs that are currently being offered. WE OFFER ALL MORTGAGE LENDING PRODUCTS. I would also like to add something in reference to the rate but I don't think it's legal to actually state or promise a rate for mortgage since they vary based on loan type, client and other criteria...

On the Harborline real estate site I would like to add a link or some way for clients to be able to put in credit card information to render services ...

Please let me know what you need from me

Thank you !!

Current link to site to improve and code

https://harborlinelendingandcapital.example/

Industry/Entity Type

Residential and commmercial lending

Coding

Coded - Design and coding required

Number of Pages Required

2 page

Requirements
Must have
• Love to integrate Mortgage interest rates even if general
Nice to have
• Link to fill out mortgage application via Quorvel LPX software

```html
<!DOCTYPE html>
<html lang="en">
<head>
<meta charset="utf-8">
<title>Harborline Lending and Capital</title>
<link href="https://fonts.googleapis.com/css2?family=Fira+Sans:wght@400;500;600;700&family=Source+Sans+3:wght@400;600&display=swap" rel="stylesheet">
<style>
:root{
  --forest:#1d3a20;
  --forest-card:#265a2e;
  --ink:#1c3b1f;
  --lime:#8dc63f;
  --lime-dark:#7fb534;
  --cream:#f5f9ec;
  --text:#3a3f3a;
  --white:#fff;
  --line:#d8dccd;
}
*{box-sizing:border-box;margin:0;padding:0}
html,body{width:1200px;height:4441px;overflow:hidden}
body{font-family:"Source Sans 3",sans-serif;color:var(--text);background:var(--white);position:relative}
h1,h2,h3,.btn,.nav a,.brand-name{font-family:"Fira Sans",sans-serif}
.abs{position:absolute}
section,header,footer,.topbar{position:absolute;left:0;width:1200px}

.topbar{top:0;height:47px;background:var(--forest);color:var(--white);font-size:13px}
.topbar .socials{left:84px;top:16px;display:flex;gap:14px}
.dot{width:13px;height:13px;border-radius:50%;background:var(--lime);display:block}
.topbar .contacts{right:86px;top:14px;display:flex;gap:18px;align-items:center}
.topbar .contacts span{display:flex;align-items:center;gap:6px}

header{top:47px;height:119px;background:var(--white)}
.brand{display:flex;align-items:center;gap:10px}
.brand-mark{width:46px;height:46px;border-radius:50%;background:var(--forest);flex:none}
.brand-name{font-size:13px;font-weight:700;color:var(--forest);letter-spacing:.5px;line-height:1.3;text-transform:uppercase}
header .brand{left:86px;top:36px}
.nav{position:absolute;top:46px;left:553px;display:flex;gap:50px;font-size:14px;font-weight:600}
.nav a{color:#1b1b1b;text-decoration:none}
.nav a.active{color:var(--lime)}
.btn{display:inline-flex;align-items:center;justify-content:center;gap:7px;background:var(--lime);color:var(--forest);font-weight:600;font-size:14px;text-decoration:none}
.btn svg{width:14px;height:14px}
header .btn{position:absolute;left:979px;top:36px;width:135px;height:41px}

.hero{top:166px;height:584px;background:linear-gradient(100deg,#3d4a44 0%,#6e7a74 45%,#b9bcb4 100%)}
.hero .veil{inset:0;background:linear-gradient(90deg,rgba(20,30,25,.55),rgba(20,30,25,0) 70%)}
.hero h1{left:83px;top:148px;font-size:46px;line-height:58px;font-weight:600;color:var(--white)}
.hero h1 em{font-style:normal;color:var(--lime)}
.hero p{left:86px;top:340px;font-size:16px;color:var(--white)}
.hero .btn{position:absolute;left:86px;top:392px;width:150px;height:42px}
.slides{left:86px;top:520px;display:flex;align-items:center;gap:10px;color:var(--white);font-size:12px}
.slides b{font-size:22px;font-weight:400;color:var(--lime)}
.slides i{width:104px;height:1px;background:rgba(255,255,255,.6);display:block}

.label{display:flex;align-items:center;gap:8px;font-family:"Fira Sans",sans-serif;font-size:12px;letter-spacing:3px;color:var(--lime);text-transform:uppercase;font-weight:500}
.label .dot{width:20px;height:20px;background:var(--forest)}
h2{font-size:44px;font-weight:600;color:var(--ink);line-height:50px}
h2 em{font-style:normal;color:var(--lime)}

.about{top:750px;height:600px}
.about .frame{left:107px;top:83px;width:458px;height:415px;border:1.5px solid var(--forest);border-radius:30px}
.about .photo{left:116px;top:92px;width:449px;height:406px;border-radius:26px;background:linear-gradient(120deg,#2f2f33 0%,#7c8791 55%,#c9d4dd 100%)}
.about .label{left:612px;top:122px;position:absolute}
.about h2{left:612px;top:160px}
.about .copy{left:612px;top:278px;width:450px;font-size:15px;line-height:26px}
.about .btn{position:absolute;left:612px;top:408px;width:152px;height:44px}
.call{left:793px;top:412px;display:flex;gap:12px;align-items:center}
.call small{display:block;font-size:11px;letter-spacing:1.5px;font-weight:600;color:#1b1b1b}
.call strong{display:block;font-size:18px;color:var(--lime);font-family:"Fira Sans",sans-serif;font-weight:600}

.services{top:1350px;height:658px;background:var(--cream)}
.services .label{position:absolute;left:0;width:1200px;justify-content:center;top:62px}
.services h2{left:0;width:1200px;text-align:center;top:96px}
.card{position:absolute;top:176px;width:323px;height:400px}
.card .pic{width:323px;height:240px;background:linear-gradient(140deg,#d8d2c8,#7d6a5a 60%,#e7e4de)}
.card .box{position:absolute;left:17px;top:219px;width:289px;height:206px;background:var(--forest-card);border-radius:3px;padding:34px 18px 0;color:var(--white)}
.card h3{font-size:17px;font-weight:600;margin-bottom:12px}
.card p{font-size:14.5px;line-height:25px;color:#dfe9da}
.more{display:inline-flex;gap:8px;align-items:center;margin-top:10px;color:var(--lime);font-size:13.5px;font-weight:600;border-bottom:1px solid var(--lime);padding-bottom:3px;font-family:"Fira Sans",sans-serif}

.properties{top:2008px;height:661px;background:var(--forest)}
.properties .label{position:absolute;left:86px;top:112px}
.properties h2{left:86px;top:136px;color:var(--white)}
.properties .btn{position:absolute;left:936px;top:130px;width:178px;height:43px}
.prop{position:absolute;top:218px;width:245px;height:346px;background:linear-gradient(180deg,#9cc1e6 0%,#e4e8ec 45%,#8a8d86 100%);overflow:hidden}
.prop .tag{position:absolute;left:0;bottom:0;height:42px;width:190px;background:var(--lime);clip-path:polygon(0 0,82% 0,100% 100%,0 100%);color:var(--white);font-family:"Fira Sans",sans-serif;font-size:16px;font-weight:500;padding:12px 0 0 10px}

.rates{top:2669px;height:653px;background:var(--cream)}
.rates .disc1{left:366px;top:174px;width:192px;height:260px;border-radius:0 130px 130px 0;background:var(--lime)}
.rates .disc2{left:138px;top:350px;width:160px;height:220px;border-radius:110px 0 0 110px;background:var(--lime)}
.rates .person{left:185px;top:38px;width:320px;height:615px;border-radius:140px 140px 0 0;background:linear-gradient(180deg,#a7806a 0%,#2b3550 30%,#1e2840 100%)}
.rates .label{position:absolute;left:616px;top:108px}
.rates h2{left:612px;top:140px}
.rates .copy{left:612px;top:200px;width:500px;font-size:15px;line-height:25px}
.panel{left:612px;top:272px;width:502px;height:254px;background:#e4e7dc;border:1px solid #cdd1c3;border-radius:16px;padding:42px 34px 0;font-size:13.5px;color:#1b1b1b}
.scale{display:flex;justify-content:space-between}
.track{position:relative;height:4px;background:#c9cdc0;border-radius:2px;margin:20px 0 38px}
.track i{position:absolute;left:0;top:0;height:4px;width:43%;background:var(--forest-card);border-radius:2px}
.track b{position:absolute;left:43%;top:-6px;width:16px;height:16px;border-radius:50%;background:var(--lime-dark);border:2px solid var(--forest-card)}
.panel .btn{position:absolute;right:34px;top:186px;width:152px;height:40px;font-size:13.5px}

.contact{top:3322px;height:661px;background:var(--white)}
.contact .label{position:absolute;left:0;width:1200px;justify-content:center;top:122px}
.contact h2{left:0;width:1200px;text-align:center;top:146px}
.contact .lead{left:0;width:1200px;text-align:center;top:198px;font-size:15px;color:#2a2a2a}
.field{position:absolute;background:var(--cream);border:1px solid var(--line);font-size:13px;color:#555;padding:13px 14px}
.contact .btn{position:absolute;left:531px;top:524px;width:138px;height:45px}

footer{top:3983px;height:458px;background:var(--forest);color:var(--white);font-size:13.5px}
footer .brand{left:86px;top:110px}
footer .brand-mark{background:var(--white)}
footer .brand-name{color:var(--white)}
footer .about-text{left:86px;top:220px;width:270px;line-height:25px}
footer h4{font-family:"Fira Sans",sans-serif;font-size:13.5px;letter-spacing:2px;color:var(--lime);font-weight:600;margin-bottom:26px}
.fcol{position:absolute;top:106px}
.fcol ul{list-style:none;line-height:38px}
.frow{display:flex;gap:10px;align-items:flex-start;line-height:22px;margin-bottom:18px}
.fsocial{display:flex;gap:28px;margin-top:4px}
.fsocial i{width:14px;height:14px;background:var(--white);border-radius:3px;display:block}
.copyright{left:86px;top:400px;width:1028px;display:flex;align-items:center;gap:14px;font-size:13px}
.copyright span em{font-style:normal;color:var(--lime)}
.copyright hr{flex:1;border:0;border-top:1px solid rgba(255,255,255,.4)}
</style>
</head>
<body>

<div class="topbar">
  <div class="abs socials"><i class="dot"></i><i class="dot"></i><i class="dot"></i></div>
  <div class="abs contacts">
    <span><svg width="13" height="13" viewBox="0 0 24 24" fill="#8dc63f"><path d="M6.6 10.8a15 15 0 006.6 6.6l2.2-2.2a1 1 0 011-.25 11.4 11.4 0 003.6.6 1 1 0 011 1V20a1 1 0 01-1 1A17 17 0 013 4a1 1 0 011-1h3.5a1 1 0 011 1c0 1.25.2 2.45.6 3.6a1 1 0 01-.25 1z"/></svg>1800 555 0147</span>
    <span><svg width="13" height="11" viewBox="0 0 24 18" fill="#8dc63f"><path d="M0 0h24v2L12 9 0 2zM0 4l12 7 12-7v14H0z"/></svg>hello@harborlinelending.example</span>
  </div>
</div>

<header>
  <div class="abs brand"><span class="brand-mark"></span><span class="brand-name">Harborline Lending and Capital of Florida<br>Business and Commercial Division</span></div>
  <nav class="nav"><a class="active" href="#">Home</a><a href="#">About Us</a><a href="#">Our Services</a><a href="#">Properties</a></nav>
  <a class="btn" href="#">Contact Us <svg viewBox="0 0 16 16"><circle cx="8" cy="8" r="8" fill="#1d3a20"/><path d="M5.5 10.5l5-5M6.5 5.5h4v4" stroke="#8dc63f" stroke-width="1.5" fill="none"/></svg></a>
</header>

<section class="hero" role="img" aria-label="Photo of a client signing a mortgage contract beside a small model house">
  <div class="abs veil"></div>
  <h1 class="abs">Your best resource<br>For hassle-free, Low cost<br><em>Mortgage Origination</em></h1>
  <p class="abs">Residential home loans in florida and commercial lending in america</p>
  <a class="btn" href="#">Know More <svg viewBox="0 0 16 16"><circle cx="8" cy="8" r="8" fill="#1d3a20"/><path d="M5.5 10.5l5-5M6.5 5.5h4v4" stroke="#8dc63f" stroke-width="1.5" fill="none"/></svg></a>
  <div class="abs slides"><b>01</b><i></i><span>04</span></div>
</section>

<section class="about">
  <div class="abs frame"></div>
  <div class="abs photo" role="img" aria-label="Portrait of a smiling loan advisor with arms crossed in an office"></div>
  <div class="label"><span class="dot"></span>About</div>
  <h2 class="abs">Harborline Mortgage<br>and Finance</h2>
  <p class="abs copy">Harborline Mortgage Originates Residential Home loans in Florida and Commercial and business financing in all 50 States. We have over 25 years of experience in ALL types of real estate and commercial lending.</p>
  <a class="btn" href="#">Learn More <svg viewBox="0 0 16 16"><circle cx="8" cy="8" r="8" fill="#1d3a20"/><path d="M5.5 10.5l5-5M6.5 5.5h4v4" stroke="#8dc63f" stroke-width="1.5" fill="none"/></svg></a>
  <div class="abs call">
    <svg width="26" height="26" viewBox="0 0 24 24" fill="#1d3a20"><path d="M6.6 10.8a15 15 0 006.6 6.6l2.2-2.2a1 1 0 011-.25 11.4 11.4 0 003.6.6 1 1 0 011 1V20a1 1 0 01-1 1A17 17 0 013 4a1 1 0 011-1h3.5a1 1 0 011 1c0 1.25.2 2.45.6 3.6a1 1 0 01-.25 1z"/></svg>
    <div><small>CALL US</small><strong>1800-555-0147</strong></div>
  </div>
</section>

<section class="services">
  <div class="label"><span class="dot"></span>Services</div>
  <h2 class="abs">What We Do <em>For You</em></h2>
  <article class="card" style="left:84px">
    <div class="pic" role="img" aria-label="Family holding a model house and keys"></div>
    <div class="box"><h3>Residential Home Mortgages</h3><p>Curabitur quis henulla. Suspendisse sit amet sales arcu. Aenean pharetra varius ultricie</p><span class="more">Learn More <svg width="13" height="13" viewBox="0 0 16 16"><circle cx="8" cy="8" r="8" fill="#8dc63f"/><path d="M5.5 10.5l5-5M6.5 5.5h4v4" stroke="#265a2e" stroke-width="1.6" fill="none"/></svg></span></div>
  </article>
  <article class="card" style="left:438px">
    <div class="pic" role="img" aria-label="Business owner at a desk with a piggy bank"></div>
    <div class="box"><h3>Professional Business Loan</h3><p>Curabitur quis henulla. Suspendisse sit amet sales arcu. Aenean pharetra varius ultricie</p><span class="more">Learn More <svg width="13" height="13" viewBox="0 0 16 16"><circle cx="8" cy="8" r="8" fill="#8dc63f"/><path d="M5.5 10.5l5-5M6.5 5.5h4v4" stroke="#265a2e" stroke-width="1.6" fill="none"/></svg></span></div>
  </article>
  <article class="card" style="left:791px">
    <div class="pic" role="img" aria-label="Couple saving coins together"></div>
    <div class="box"><h3>Investment Properties Loan</h3><p>Curabitur quis henulla. Suspendisse sit amet sales arcu. Aenean pharetra varius ultricie</p><span class="more">Learn More <svg width="13" height="13" viewBox="0 0 16 16"><circle cx="8" cy="8" r="8" fill="#8dc63f"/><path d="M5.5 10.5l5-5M6.5 5.5h4v4" stroke="#265a2e" stroke-width="1.6" fill="none"/></svg></span></div>
  </article>
</section>

<section class="properties">
  <div class="label"><span class="dot"></span>Properties</div>
  <h2 class="abs">Available Properties</h2>
  <a class="btn" href="#">View All Propertie <svg viewBox="0 0 16 16"><circle cx="8" cy="8" r="8" fill="#1d3a20"/><path d="M5.5 10.5l5-5M6.5 5.5h4v4" stroke="#8dc63f" stroke-width="1.5" fill="none"/></svg></a>
  <div class="prop" style="left:84px" role="img" aria-label="White apartment building with glass balconies"><span class="tag">12 Sunset Street</span></div>
  <div class="prop" style="left:346px" role="img" aria-label="Modern stacked apartment block"><span class="tag">34 Union Avenue</span></div>
  <div class="prop" style="left:608px" role="img" aria-label="Brick and white residential tower"><span class="tag">56 Washington Street</span></div>
  <div class="prop" style="left:869px" role="img" aria-label="Townhouse building with palm trees"><span class="tag">78 Oak Boulevard</span></div>
</section>

<section class="rates">
  <div class="abs disc1"></div>
  <div class="abs disc2"></div>
  <div class="abs person" role="img" aria-label="Loan officer in a suit holding house keys and cash"></div>
  <div class="label"><span class="dot"></span>Interest Rates</div>
  <h2 class="abs">Mortgage Interest Rates</h2>
  <p class="abs copy">Vivamus mattis augue vitae velit congue vestibulum. Curabitur ultricies, metus id lacinia accumsan, nisl dui eleifend augue.</p>
  <div class="abs panel">
    <div class="scale"><span>$ 1000</span><span>$ 25,000</span><span>$ 50,000</span></div>
    <div class="track"><i></i><b></b></div>
    <div class="scale"><span>1Month</span><span>6 Month</span><span>12Month</span></div>
    <div class="track"><i></i><b></b></div>
    <a class="btn" href="#">Apply For Loan <svg viewBox="0 0 16 16"><circle cx="8" cy="8" r="8" fill="#1d3a20"/><path d="M5.5 10.5l5-5M6.5 5.5h4v4" stroke="#8dc63f" stroke-width="1.5" fill="none"/></svg></a>
  </div>
</section>

<section class="contact">
  <div class="label"><span class="dot"></span>Contact Us</div>
  <h2 class="abs">Get In Touch</h2>
  <p class="abs lead">Fusce auctor erat erat, eu pulvinar neque iaculis sit amet. Duis ac odio tincidunt</p>
  <div class="field" style="left:276px;top:252px;width:315px;height:45px">Name</div>
  <div class="field" style="left:607px;top:252px;width:317px;height:45px">Email</div>
  <div class="field" style="left:276px;top:316px;width:315px;height:43px">Phone</div>
  <div class="field" style="left:607px;top:316px;width:317px;height:43px">Subject</div>
  <div class="field" style="left:276px;top:378px;width:648px;height:124px">How Can We Help You...</div>
  <a class="btn" href="#">Submit <svg viewBox="0 0 16 16"><circle cx="8" cy="8" r="8" fill="#1d3a20"/><path d="M5.5 10.5l5-5M6.5 5.5h4v4" stroke="#8dc63f" stroke-width="1.5" fill="none"/></svg></a>
</section>

<footer>
  <div class="abs brand"><span class="brand-mark"></span><span class="brand-name">Harborline Lending and Capital of Florida<br>Business and Commercial Division</span></div>
  <p class="abs about-text">Harborline Mortgage Originates Residential Home loans in Florida and Commercial and business financing in all 50 States. We have over 25 years</p>
  <div class="fcol" style="left:460px">
    <h4>CONTACT INFO</h4>
    <div class="frow"><svg width="14" height="11" viewBox="0 0 24 18" fill="#8dc63f" style="margin-top:6px"><path d="M0 0h24v2L12 9 0 2zM0 4l12 7 12-7v14H0z"/></svg><span>hello@harborline<br>lending.example</span></div>
    <div class="frow"><svg width="14" height="14" viewBox="0 0 24 24" fill="#8dc63f" style="margin-top:4px"><path d="M6.6 10.8a15 15 0 006.6 6.6l2.2-2.2a1 1 0 011-.25 11.4 11.4 0 003.6.6 1 1 0 011 1V20a1 1 0 01-1 1A17 17 0 013 4a1 1 0 011-1h3.5a1 1 0 011 1c0 1.25.2 2.45.6 3.6a1 1 0 01-.25 1z"/></svg><span>1800-555-0147</span></div>
  </div>
  <div class="fcol" style="left:785px">
    <h4>QUICK LINKS</h4>
    <ul><li>Home</li><li>About Us</li><li>Our Services</li><li>Properties</li><li>Contact Us</li></ul>
  </div>
  <div class="fcol" style="left:1014px">
    <h4>FOLLOW US</h4>
    <div class="fsocial"><i></i><i></i><i></i></div>
  </div>
  <div class="abs copyright"><span>© 2025 <em>Harborline Lending and Capital Of Florida</em>. All right reserved.</span><hr><span>January 08, 2025. Layout_4</span></div>
</footer>

</body>
</html>
```